business card

Business card for new business.
Red and black corporate colors.
Card can have an Indsutrial feel to it. Feel free to add Rust, Bolted steel, or graphics as you see fit. We provide highly specialized services to the below mentioned industries.
Keep information out of corners so that if I want I can choose rounded corners.
Information
- front. name - title - phone - email
- Rear
Refining - Rail - Infrastructure - Mining - Energy
Calgary - Edmonton - Fort McMurray - Revelstoke - Vancouver

```html
<!DOCTYPE html>
<html lang="en">
<head>
<meta charset="utf-8">
<title>Ironvale Business Card</title>
<link href="https://fonts.googleapis.com/css2?family=Roboto:wght@400;500&family=Roboto+Condensed:wght@700&display=swap" rel="stylesheet">
<style>
  :root {
    --backdrop: #2b2b2b;
    --paper: #f3f3f3;
    --brand-red: #e30613;
    --steel-grey: #7a7a7a;
    --ink-grey: #555555;
    --white: #ffffff;
  }
  * { margin: 0; padding: 0; box-sizing: border-box; }
  html, body {
    width: 1200px; height: 960px; overflow: hidden;
    background: var(--backdrop);
    font-family: "Roboto", Arial, sans-serif;
  }
  .card {
    position: absolute;
    width: 600px; height: 343px;
  }
  .card--front { left: 314px; top: 113px; background: var(--paper); }
  .card--back { left: 311px; top: 472px; background: var(--brand-red); }

  .wordmark {
    position: absolute; left: 74px; top: 141px;
    font-family: "Roboto Condensed", "Arial Narrow", sans-serif;
    font-weight: 700; font-size: 50px; line-height: 58px;
    color: var(--steel-grey); letter-spacing: 1px;
  }
  .divider {
    position: absolute; left: 348px; top: 119px;
    width: 2px; height: 106px; background: #d0d0d0;
  }
  .contact { position: absolute; left: 372px; top: 124px; }
  .contact__name {
    font-family: "Roboto Condensed", "Arial Narrow", sans-serif;
    font-weight: 700; font-size: 24px; line-height: 28px;
    color: var(--brand-red);
  }
  .contact__title {
    font-size: 15px; line-height: 18px; color: var(--steel-grey);
    margin-bottom: 10px;
  }
  .contact__line {
    display: flex; align-items: center; gap: 8px;
    font-size: 14.5px; line-height: 20px; color: var(--ink-grey);
  }
  .contact__line svg { width: 14px; height: 14px; flex: none; }

  .web-arrow { position: absolute; left: 0; top: 287px; width: 556px; height: 44px; }
  .web-arrow__text {
    position: absolute; left: 0; top: 297px; width: 534px;
    text-align: center; font-size: 13px; line-height: 24px;
    letter-spacing: 5.5px; color: var(--white); font-weight: 500;
  }

  .back-name {
    position: absolute; left: 0; top: 122px; width: 100%;
    text-align: center;
    font-family: "Roboto Condensed", "Arial Narrow", sans-serif;
    font-weight: 700; font-size: 44px; color: var(--white);
  }
  .services {
    position: absolute; left: 0; top: 256px; width: 100%;
    text-align: center; color: var(--white);
    font-size: 14.5px; line-height: 18px;
  }
</style>
</head>
<body>
  <section class="card card--front">
    <div class="wordmark">IRONVALE</div>
    <div class="divider"></div>
    <div class="contact">
      <div class="contact__name">DANIEL REYES</div>
      <div class="contact__title">CEO/FOUNDER</div>
      <div class="contact__line">
        <svg viewBox="0 0 24 24" aria-hidden="true"><path fill="#e30613" d="M6.6 10.8a15 15 0 0 0 6.6 6.6l2.2-2.2c.3-.3.7-.4 1-.2 1.1.4 2.3.6 3.6.6.6 0 1 .4 1 1V20c0 .6-.4 1-1 1A17 17 0 0 1 3 4c0-.6.4-1 1-1h3.5c.6 0 1 .4 1 1 0 1.3.2 2.5.6 3.6.1.3 0 .7-.2 1z"/></svg>
        <span>604 555 0147</span>
      </div>
      <div class="contact__line">
        <svg viewBox="0 0 24 24" aria-hidden="true"><rect x="2" y="5" width="20" height="14" fill="#e30613"/><path d="M2 5l10 8 10-8" fill="none" stroke="#f3f3f3" stroke-width="2"/></svg>
        <span>info@ironvale.com</span>
      </div>
    </div>
    <svg class="web-arrow" viewBox="0 0 556 44" aria-hidden="true">
      <polygon fill="#e30613" points="0,10 524,10 524,0 556,22 524,44 524,34 0,34"/>
    </svg>
    <div class="web-arrow__text">www.ironvale.com</div>
  </section>

  <section class="card card--back">
    <div class="back-name">IRONVALE</div>
    <div class="services">
      Welding • Piping • Fabrication • Rigging<br>
      Marine • Halden • Brookport • North Carraway<br>
      Millbrook • Westhaven
    </div>
  </section>
</body>
</html>
```